Bright Net Rally Website Design (design layout only)

We need a website design for a new nonprofit organization based in Des Moines, Iowa called Bright Net Rally. The nonprofit provides soccer training opportunities to youth soccer players looking to improve their game while also affecting the lives of the less fortunate in a positive way. While participating in the training programs the players also go out and raise money for selected charities. The organization then donates the funds. In its first 18 months we donated $10,500. We would like to see designs attempt to symbolize the mission of the nonprofit - essentially "improve you while improving someone else."

We would like to see the following features:

· A place to donate - Our intent is to have the home page linked to the donation page; a simple straight-forward process for people to give money, and make donating as painless as possible - no account needed to make a donation, credit card or e-check should be the only information needed to donate, and have it be on a single page.

· A photo gallery so people can browse the photo gallery to get a better understanding of our organization and a place to add videos and a calendar to show upcoming events

· A place for contact information and the profiles of directors and board members. This should include a spot showing all the charities the organization donates to. Also includes a news section/blog for comments and suggestions.

We want the design to revolve around the content and mission. We would really like to stress our organization as nonprofit. We would also like if the website was user friendly and easy to navigate.

The logo of our organization is uploaded

```html
<!DOCTYPE html>
<html lang="en">
<head>
<meta charset="utf-8">
<title>Bright Net Rally</title>
<link href="https://fonts.googleapis.com/css2?family=Ubuntu:wght@400;500;700&family=Lora:ital@1&display=swap" rel="stylesheet">
<style>
:root{
  --green:#56b52b;
  --green-dark:#2f5d1c;
  --text:#5a5a5a;
  --heading:#2b2b2b;
  --line:#e4e4e4;
  --footer:#3e3e42;
  --footer-bottom:#262628;
  --footer-text:#e6e6e6;
  --white:#ffffff;
}
*{box-sizing:border-box;margin:0;padding:0}
a{text-decoration:none}
html,body{width:1200px;height:2595px;overflow:hidden}
body{font-family:"Ubuntu",sans-serif;color:var(--text);background:var(--white);position:relative}
.abs{position:absolute}

/* header */
.site-header{position:absolute;left:0;top:0;width:1200px;height:112px;background:var(--white)}
.brand{position:absolute;left:140px;top:36px;display:flex;align-items:center;gap:10px;font-weight:700;font-size:22px;color:var(--green-dark)}
.brand-mark{width:22px;height:22px;background:var(--green)}
.main-nav{position:absolute;right:150px;top:52px;display:flex;gap:40px;font-size:15px;font-weight:500;letter-spacing:.5px}
.main-nav a{color:var(--heading)}
.main-nav a.active{color:var(--green)}

/* hero */
.hero{position:absolute;left:0;top:112px;width:1200px;height:487px;
  background:
    radial-gradient(ellipse 190px 230px at 820px 330px,rgba(196,196,190,.95),rgba(196,196,190,0) 100%),
    radial-gradient(ellipse 170px 200px at 560px 380px,rgba(206,204,198,.95),rgba(206,204,198,0) 100%),
    radial-gradient(ellipse 70px 85px at 800px 150px,rgba(150,105,80,.85),rgba(150,105,80,0) 100%),
    radial-gradient(ellipse 62px 75px at 545px 250px,rgba(205,160,130,.85),rgba(205,160,130,0) 100%),
    radial-gradient(ellipse 130px 260px at 110px 300px,rgba(205,200,190,.75),rgba(205,200,190,0) 100%),
    radial-gradient(ellipse 120px 240px at 370px 260px,rgba(190,185,175,.7),rgba(190,185,175,0) 100%),
    radial-gradient(ellipse 120px 240px at 1110px 300px,rgba(210,205,200,.75),rgba(210,205,200,0) 100%),
    radial-gradient(ellipse 260px 120px at 980px 60px,rgba(230,240,200,.7),rgba(230,240,200,0) 100%),
    linear-gradient(180deg,#7f9a55 0%,#9bb26a 35%,#8ea866 60%,#7d8f66 100%)}
.donate-btn{position:absolute;left:465px;top:566px;width:270px;height:66px;border-radius:33px;background:var(--green);border:4px solid #e9f3e1;color:var(--white);font-weight:700;font-size:27px;display:flex;align-items:center;justify-content:center;box-shadow:0 3px 8px rgba(0,0,0,.25)}

/* welcome */
.welcome-eyebrow{left:140px;top:676px;font-family:"Lora",serif;font-style:italic;font-size:17px;color:#444}
.welcome-title{left:140px;top:694px;font-size:29px;font-weight:700;color:var(--green-dark)}
.welcome-copy{left:140px;top:732px;width:470px;font-size:14px;line-height:24.5px}
.welcome-copy p+p{margin-top:24px}
.video{left:672px;top:694px;width:384px;height:280px;border:4px solid #eee;
  background:
    radial-gradient(ellipse 80px 110px at 120px 200px,rgba(120,120,120,.8),rgba(120,120,120,0)),
    radial-gradient(ellipse 90px 130px at 250px 170px,rgba(130,130,130,.8),rgba(130,130,130,0)),
    linear-gradient(135deg,#3a3a3a,#555 60%,#444);box-shadow:0 2px 6px rgba(0,0,0,.2)}
.video svg{position:absolute;left:166px;top:114px}

.section-shadow{left:0;width:1200px;height:30px;background:linear-gradient(180deg,rgba(0,0,0,.06),rgba(0,0,0,0))}
.section-heading{font-size:28px;font-weight:700;color:var(--green-dark);letter-spacing:.5px}
.pill{height:28px;padding:0 14px;border-radius:14px;background:var(--green);color:var(--white);font-size:12px;display:flex;align-items:center}

/* gallery */
.gallery-grid{left:140px;top:1124px;width:583px;height:282px;display:grid;grid-template-columns:repeat(4,1fr);grid-template-rows:repeat(2,1fr);gap:4px}
.tile-a{background:linear-gradient(160deg,#d9d6cf,#5a7fae 55%,#2e3b52)}
.tile-b{background:linear-gradient(180deg,#cfd6c4,#c9a58a 40%,#cfcfcb 75%,#bbb)}
.tile-c{background:linear-gradient(180deg,#e4e6e3,#c99e80 35%,#9aa3ad 70%,#6d747c)}
.tile-d{background:linear-gradient(150deg,#c5b9a2,#6b4a3a 45%,#2f78b8 80%)}
.tile-e{background:linear-gradient(180deg,#e2e4e6,#caa488 35%,#8d949b 70%,#5d6268)}
.tile-f{background:linear-gradient(170deg,#b99c7c,#6e4a38 40%,#3a84c5 80%)}
.tile-g{background:linear-gradient(180deg,#a4b77f,#caa58a 40%,#d0cfca 75%,#b7b7b2)}
.tile-h{background:linear-gradient(160deg,#d7d8d8,#4e74a6 55%,#c1c6cc)}

/* calendar */
.calendar{left:778px;top:1124px;width:282px}
.cal-head{height:48px;background:var(--green);color:var(--white);display:flex;align-items:center;justify-content:space-between;padding:0 12px;font-size:17px;font-weight:500}
.cal-table{width:100%;border-collapse:collapse;font-size:12px;text-align:center;table-layout:fixed}
.cal-table th{height:34px;color:#333;font-weight:700;font-size:14px;border:1px solid var(--line)}
.cal-table td{height:36px;border:1px solid var(--line);background:#f3f3f3;color:#444}
.cal-table td.empty{background:var(--white)}
.cal-table td.event{background:var(--green);color:var(--white)}

/* team */
.member{display:flex;gap:20px}
.avatar{width:152px;height:152px;border-radius:50%;border:6px solid #f0f0f0;box-shadow:0 2px 6px rgba(0,0,0,.15);flex:none;
  background:radial-gradient(ellipse 34px 42px at 50% 40%,#d9b294,rgba(217,178,148,0) 100%),linear-gradient(180deg,#eef1f3 0%,#dfe5ea 55%,#3a4656 78%,#2a3340 100%)}
.avatar.alt{background:radial-gradient(ellipse 34px 42px at 50% 40%,#dcb699,rgba(220,182,153,0) 100%),linear-gradient(180deg,#b8d3e6 0%,#cfdde8 55%,#3c5a80 78%,#2d4260 100%)}
.member-info{padding-top:24px;width:250px;font-size:14px;line-height:24px}
.member-name{font-weight:700;color:var(--green-dark);font-size:15px}
.member-name span{font-weight:400;color:var(--text)}
.divider-v{left:599px;top:1590px;width:1px;height:395px;background:var(--line)}
.divider-h{left:623px;top:1773px;width:437px;height:1px;background:var(--line)}

/* footer */
.site-footer{left:0;top:2075px;width:1200px;height:450px;background:var(--footer);color:var(--footer-text)}
.footer-title{font-size:18px;font-weight:500;color:var(--white)}
.footer-links{list-style:none;font-size:13px}
.footer-links li{height:34.5px;position:relative;padding-left:20px}
.footer-links li::before{content:"";position:absolute;left:0;top:7px;width:4px;height:4px;background:#777}
.news-item{display:flex;gap:16px;width:330px}
.news-thumb{width:68px;height:68px;border:3px solid #fff;flex:none;
  background:radial-gradient(ellipse 14px 17px at 50% 42%,#d4ad90,rgba(212,173,144,0)),linear-gradient(180deg,#dfe3e6,#c8ced3 60%,#7e8a96)}
.news-body{width:230px}
.news-item h4{font-size:13px;font-weight:700;color:var(--white);margin-bottom:4px}
.news-item p{font-size:12.5px;line-height:19px;font-weight:500}
.news-item a{color:var(--green)}
.contact-row{display:flex;gap:20px;font-size:12.5px;font-weight:700;line-height:20px;width:300px}
.contact-icon{width:28px;height:28px;background:#111;flex:none;display:flex;align-items:center;justify-content:center}
.contact-row a{color:var(--green)}
.subscribe{left:765px;top:2452px;width:246px;height:28px;display:flex}
.subscribe-field{flex:1;border-bottom:2px solid var(--green)}
.subscribe-btn{width:28px;height:28px;background:#111;display:flex;align-items:center;justify-content:center}
.footer-bottom{left:0;top:2525px;width:1200px;height:70px;background:var(--footer-bottom);color:#ddd}
.copyright{left:140px;top:27px;font-size:12px}
.social{left:886px;top:20px;display:flex;gap:8px}
.social span{width:28px;height:28px;border-radius:50%;background:#6b6b6e}
</style>
</head>
<body>

<header class="site-header">
  <div class="brand"><span class="brand-mark"></span>Bright Net Rally</div>
  <nav class="main-nav">
    <a class="active" href="#">HOME</a><a href="#">ABOUT</a><a href="#">SERVICES</a><a href="#">PLAYER</a><a href="#">DONATION</a><a href="#">CONTACT US</a>
  </nav>
</header>

<section class="hero" role="img" aria-label="Photo of smiling young volunteers in grey volunteer shirts outdoors in a sunny park"></section>
<a class="donate-btn" href="#">DONATION NOW</a>

<div class="abs welcome-eyebrow">Welcome to</div>
<h1 class="abs welcome-title">BRIGHT NET RALLY</h1>
<div class="abs welcome-copy">
  <p>Lorem Ipsum is simply dummy text of the printing and typesetting industry. Lorem Ipsum has been the industry's standard dummy text ever since the 1500s, when an unknown printer took a galley of type and scrambled it to make a type specimen book. It has survived not only five centuries, but also the leap into electronic typesetting, remaining essentially</p>
  <p>Lorem Ipsum is simply dummy text of the printing and typesetting industry. Lorem Ipsum has been the industry's standard dummy text when an unknown printer took a galley.</p>
</div>
<div class="abs video" role="img" aria-label="Video still of two volunteers, with a play button">
  <svg width="52" height="52" viewBox="0 0 52 52"><circle cx="26" cy="26" r="23" fill="none" stroke="#fff" stroke-width="3"/><path d="M21 15 L37 26 L21 37 Z" fill="#fff"/></svg>
</div>

<div class="abs section-shadow" style="top:1027px"></div>
<h2 class="abs section-heading" style="left:140px;top:1067px">PHOTO GALLERY</h2>
<a class="abs pill" style="left:605px;top:1078px" href="#">View All Photos</a>
<div class="abs gallery-grid" role="img" aria-label="Gallery of eight photos of volunteers and team members">
  <div class="tile-a"></div><div class="tile-b"></div><div class="tile-c"></div><div class="tile-d"></div>
  <div class="tile-e"></div><div class="tile-f"></div><div class="tile-g"></div><div class="tile-h"></div>
</div>

<h2 class="abs section-heading" style="left:778px;top:1067px">UPCOMING EVENTS</h2>
<div class="abs calendar">
  <div class="cal-head"><span>&#10094;</span><span>JULY 2014</span><span>&#10095;</span></div>
  <table class="cal-table">
    <tr><th>Su</th><th>Mo</th><th>Tu</th><th>We</th><th>Th</th><th>Fr</th><th>Sa</th></tr>
    <tr><td class="empty"></td><td class="empty"></td><td>1</td><td>2</td><td>3</td><td>4</td><td>5</td></tr>
    <tr><td>6</td><td>7</td><td>8</td><td>9</td><td>10</td><td>11</td><td>12</td></tr>
    <tr><td>13</td><td>14</td><td>15</td><td>16</td><td>17</td><td>18</td><td>19</td></tr>
    <tr><td>20</td><td>21</td><td>22</td><td>23</td><td class="event">24</td><td>25</td><td>26</td></tr>
    <tr><td>27</td><td>28</td><td class="event">29</td><td>30</td><td>31</td><td class="empty"></td><td class="empty"></td></tr>
  </table>
</div>

<div class="abs section-shadow" style="top:1470px"></div>
<h2 class="abs section-heading" style="left:140px;top:1510px">OUR TEAM</h2>
<a class="abs pill" style="left:947px;top:1514px" href="#">View All Team</a>

<div class="abs member" style="left:140px;top:1584px">
  <div class="avatar" role="img" aria-label="Portrait of the director"></div>
  <div class="member-info"><div class="member-name">Jon Doe <span>-Director</span></div>Lorem Ipsum is simply dummy text of the printing and typesetting industry. Lorem Ipsum has been</div>
</div>
<div class="abs member" style="left:629px;top:1584px">
  <div class="avatar" role="img" aria-label="Portrait of a team member"></div>
  <div class="member-info"><div class="member-name">Member Name</div>Lorem Ipsum is simply dummy text of the printing and typesetting industry. Lorem Ipsum has been</div>
</div>
<div class="abs member" style="left:140px;top:1833px">
  <div class="avatar" role="img" aria-label="Portrait of the director"></div>
  <div class="member-info"><div class="member-name">Jon Doe <span>-Director</span></div>Lorem Ipsum is simply dummy text of the printing and typesetting industry. Lorem Ipsum has been</div>
</div>
<div class="abs member" style="left:629px;top:1833px">
  <div class="avatar alt" role="img" aria-label="Portrait of a team member"></div>
  <div class="member-info"><div class="member-name">Member Name</div>Lorem Ipsum is simply dummy text of the printing and typesetting industry. Lorem Ipsum has been</div>
</div>
<div class="abs divider-v"></div>
<div class="abs divider-h"></div>

<footer class="abs site-footer">
  <div class="abs footer-title" style="left:140px;top:48px">Support/Help</div>
  <ul class="abs footer-links" style="left:140px;top:103px">
    <li>Home</li><li>About</li><li>Services</li><li>Player</li><li>donation</li><li>Contact Us</li>
  </ul>

  <div class="abs footer-title" style="left:357px;top:44px">Latest News</div>
  <div class="abs news-item" style="left:357px;top:104px">
    <div class="news-thumb" role="img" aria-label="News photo"></div>
    <div class="news-body"><h4>Lorem Ipsum dolo consectetur elit</h4><p>Sed ut perspiciatis unde omnis iste natus error sit voluptatem accusantium...<a href="#">Read more</a></p></div>
  </div>
  <div class="abs news-item" style="left:357px;top:214px">
    <div class="news-thumb" role="img" aria-label="News photo"></div>
    <div class="news-body"><h4>Lorem Ipsum dolo consectetur elit</h4><p>Sed ut perspiciatis unde omnis iste natus error...<a href="#">Read more</a></p></div>
  </div>
  <div class="abs news-item" style="left:357px;top:324px">
    <div class="news-thumb" role="img" aria-label="News photo"></div>
    <div class="news-body"><h4>Lorem Ipsum dolo consectetur elit</h4><p>Sed ut perspiciatis unde omnis iste natus error sit...<a href="#">Read more</a></p></div>
  </div>

  <div class="abs footer-title" style="left:765px;top:48px">Contact info</div>
  <div class="abs contact-row" style="left:765px;top:104px">
    <span class="contact-icon"><svg width="12" height="16" viewBox="0 0 12 16"><path d="M6 0a6 6 0 0 1 6 6c0 4-6 10-6 10S0 10 0 6a6 6 0 0 1 6-6z" fill="#fff"/><circle cx="6" cy="6" r="2.2" fill="#111"/></svg></span>
    <div>Address: 4820 Meadow Lorem Ipsum is simply dummy text of the prin</div>
  </div>
  <div class="abs contact-row" style="left:765px;top:167px">
    <span class="contact-icon"><svg width="14" height="14" viewBox="0 0 14 14"><path d="M3 1l2 3-1.5 1.5c.8 1.8 2.2 3.2 4 4L9 8l3 2-1 3C6 13 1 8 1 3z" fill="#fff"/></svg></span>
    <div>Phone: +12 555 010-45-78<br>&nbsp;&nbsp;&nbsp;&nbsp;&nbsp;&nbsp;&nbsp;&nbsp;&nbsp;&nbsp;&nbsp;&nbsp;+12 555 010-45-79</div>
  </div>
  <div class="abs contact-row" style="left:765px;top:229px">
    <span class="contact-icon"><svg width="14" height="10" viewBox="0 0 14 10"><rect x="0.5" y="0.5" width="13" height="9" fill="#fff"/><path d="M0.5 0.5L7 6l6.5-5.5" fill="none" stroke="#111"/></svg></span>
    <div style="padding-top:4px">E-mail: <a href="#">Contact@BrightNetRally.org</a></div>
  </div>
  <div class="abs footer-title" style="left:765px;top:293px;font-size:16px">Follow Us</div>
  <div class="abs" style="left:765px;top:330px;width:300px;font-size:12.5px;font-weight:700;line-height:20px">Lorem Ipsum is simply dummy text of the printing and typesetting industry.</div>
  <div class="subscribe" style="position:absolute;top:377px">
    <div class="subscribe-field"></div>
    <div class="subscribe-btn"><svg width="14" height="10" viewBox="0 0 14 10"><rect x="0.5" y="0.5" width="13" height="9" fill="none" stroke="#fff"/><path d="M0.5 0.5L7 6l6.5-5.5" fill="none" stroke="#fff"/></svg></div>
  </div>
</footer>

<div class="abs footer-bottom">
  <div class="abs copyright">Copyright 2014 - Bright Net Rally - All Rights Reserved</div>
  <div class="abs social"><span></span><span></span><span></span><span></span><span></span><span></span></div>
</div>

</body>
</html>
```